Building company buisness cards

We are looking for a sharp modern new look for our business cards.
We are a New Zealand based company that specialises in house and land packages.
We have attached a photo of the current logo and would like to see if it can be improved somehow if needed.
We are open to any colours but we have chosen green at this stage.
Feel free to change the font and make the logo smarter looking.
Play with the colours and see what looks best.

We want a card that looks so good know one will want to throw it away!

Target Market(s)

Home buyers

Industry/Entity Type

Building

Contact Information for Business Card

Derek Tolvane
0217394062
dtolvane@quillmarkhomesteads.co.nz
quillmarkhomesteads.co.nz

Font styles to use
Serif
Sans Serif

Colors

Designer to choose colors to be used in the design.

Requirements
Must have
• Logo and company name on one side, details on the other side
Nice to have
• Color codes for the original green are HEX #4a8028, RGB(74,128,40), CMYK(42,0,69,50)
• Round corners, Raised and/or spot UV

```html
<!DOCTYPE html>
<html lang="en">
<head>
<meta charset="utf-8">
<title>Quillmark Homesteads – Business Cards</title>
<link rel="stylesheet" href="https://fonts.googleapis.com/css2?family=Arimo:wght@700&family=Open+Sans:wght@400&display=swap">
<style>
  :root {
    --stage: #1e1e1e;
    --card-black: #050505;
    --card-white: #ffffff;
    --brand-green: #4a8028;
    --swoosh-grey: #6e6e6e;
    --ink: #1a1a1a;
    --light-text: #f2f2f2;
  }
  * { margin: 0; padding: 0; box-sizing: border-box; }
  html, body {
    width: 1200px; height: 960px; overflow: hidden;
    background: var(--stage);
  }
  .canvas { position: relative; width: 1200px; height: 960px; }

  .card {
    position: absolute;
    width: 560px; height: 320px;
    border-radius: 10px;
    overflow: hidden;
    box-shadow: 0 20px 40px rgba(0,0,0,.45);
  }

  /* Back side */
  .card--back {
    left: 560px; top: 110px;
    background: var(--card-black);
    display: flex; flex-direction: column; align-items: center;
  }
  .card--back .wordmark {
    margin-top: 112px;
    display: flex; align-items: center; gap: 12px;
  }
  .wordmark__dot {
    width: 18px; height: 18px; background: var(--brand-green);
  }
  .wordmark__name {
    font-family: "Arimo", sans-serif; font-weight: 700;
    color: var(--brand-green); font-size: 34px; letter-spacing: -0.5px;
  }
  .card--back .rule {
    width: 110px; height: 1px; background: var(--brand-green);
    margin-top: 18px;
  }
  .card--back .web {
    position: absolute; right: 28px; bottom: 22px;
    font-family: "Open Sans", sans-serif; font-size: 15px;
    letter-spacing: 1.6px; color: var(--light-text);
  }
  .card--back .web span { color: var(--brand-green); }

  /* Front side */
  .card--front {
    left: 100px; top: 520px;
    background: var(--card-white);
  }
  .card--front .wordmark {
    position: absolute; left: 0; right: 0; top: 54px;
    display: flex; justify-content: center; align-items: center; gap: 12px;
  }
  .card--front .wordmark__name { font-size: 32px; }
  .holder {
    position: absolute; left: 0; right: 0; top: 124px;
    text-align: center;
    font-family: "Arimo", sans-serif; font-weight: 700;
    font-size: 24px; color: var(--brand-green);
  }
  .contacts {
    position: absolute; left: 150px; top: 170px;
    font-family: "Open Sans", sans-serif; font-size: 14px; color: var(--ink);
    list-style: none;
  }
  .contacts li { display: flex; align-items: center; gap: 8px; height: 22px; }
  .contacts li.phone { padding-left: 96px; }
  .contacts svg { width: 12px; height: 12px; fill: var(--brand-green); flex: none; }
  .swoosh { position: absolute; left: 0; bottom: 0; width: 560px; height: 320px; }
</style>
</head>
<body>
<main class="canvas">

  <section class="card card--back" aria-label="Business card back">
    <div class="wordmark">
      <span class="wordmark__dot"></span>
      <span class="wordmark__name">Quillmark Homesteads</span>
    </div>
    <div class="rule"></div>
    <p class="web">www.<span>quillmarkhomesteads</span>.co.nz</p>
  </section>

  <section class="card card--front" aria-label="Business card front">
    <svg class="swoosh" viewBox="0 0 560 320" aria-hidden="true">
      <path d="M0 150 C 20 210, 120 230, 260 250 C 400 270, 520 290, 560 320 L0 320 Z" fill="var(--swoosh-grey)"/>
      <path d="M0 178 C 40 228, 140 245, 270 262 C 410 280, 520 300, 560 320 L0 320 Z" fill="var(--card-white)"/>
      <path d="M0 190 C 50 238, 150 254, 280 270 C 420 288, 520 304, 550 320 L0 320 Z" fill="var(--brand-green)"/>
    </svg>

    <div class="wordmark">
      <span class="wordmark__dot"></span>
      <span class="wordmark__name">Quillmark Homesteads</span>
    </div>
    <h1 class="holder">Derek Tolvane</h1>
    <ul class="contacts">
      <li class="phone">
        <svg viewBox="0 0 24 24"><path d="M6.6 10.8a15 15 0 0 0 6.6 6.6l2.2-2.2a1 1 0 0 1 1-.25 11.4 11.4 0 0 0 3.6.57 1 1 0 0 1 1 1V20a1 1 0 0 1-1 1A17 17 0 0 1 3 4a1 1 0 0 1 1-1h3.5a1 1 0 0 1 1 1 11.4 11.4 0 0 0 .57 3.6 1 1 0 0 1-.25 1z"/></svg>
        0217394062
      </li>
      <li>
        <svg viewBox="0 0 24 24"><path d="M2 5h20v14H2z M2 5l10 8 10-8" fill="var(--brand-green)"/></svg>
        dtolvane@quillmarkhomesteads.co.nz
      </li>
      <li>
        <svg viewBox="0 0 24 24"><circle cx="12" cy="12" r="10"/></svg>
        www.quillmarkhomesteads.co.nz
      </li>
    </ul>
  </section>

</main>
</body>
</html>
```